Business Card: RW Office Partners - Your organised problem solver

Business Name: RW Office Partners
Website: www.rwofficepartners.com.au
Email: marisol@rwofficepartners.com.au
Mobile: 61 482 907 236
Facebook: @rwofficepartners
Instrgram: @rwofficepartners

Brading Colours:
HEX
#986474
#ddccd3
#7a8498
#c9d8e4
#000000
#ffffff

Tag Line: Your steady, sorted task helper

Link to DRAFT website:
https://deskhelpcollective.wixsite.com/rw-office-partners

About Page from the website:
My name is Marisol Wrenfield, and I would love to assist you to become more productive in your day to day and achieve your business and personal goals.
My mission is to give you time, time to work on the important tasks of your business or to be able to spend more time with your family. I will take on the tasks you don’t have time for, don’t know well or simply don’t like to do.
I have an extensive background in Administration, Tender Coordination, Document Control, WHS and Quality Management working primarily in the Construction, Mining and Corporate World.
I am passionate about being organised, having order and making things in your life (and mine) easier! I love to watch something unfold and grow into something amazing! I am known for being the go-to problem solver, the organiser of all things, producing high standards of work even under pressure. I’m also a confident communicator, and I understand that you’re busy running your business.

Target Market(s)

Small to Medium Business who require assistance in their business by a virtual assistant.

Industry/Entity Type

Virtual Assistant

Contact Information for Business Card

Mobile: 61 482 907 236

Font styles to use
Sans Serif

Colors
ffffff

Requirements
Must have
• Branding Colours as outlined.
Contact Details as outlined.
Logo as provided.
Proper contact details - mobile, facebook, instragm, website.
Simple, Elegant, very clean looking.
Should not have
• Note cute with pictures.
Not too girly as still want to market to construction companies.

```html
<!DOCTYPE html>
<html lang="en">
<head>
<meta charset="utf-8">
<title>RW Office Partners – Business Card</title>
<link rel="stylesheet" href="https://fonts.googleapis.com/css2?family=Montserrat:wght@500;600;700&family=Roboto:wght@400;500&display=swap">
<style>
  :root {
    --backdrop: #3b3b3d;
    --card: #222023;
    --mauve: #986474;
    --blush: #ddccd3;
    --slate: #7a8498;
    --mist: #c9d8e4;
    --white: #ffffff;
  }
  * { box-sizing: border-box; margin: 0; padding: 0; }
  html, body { width: 799px; height: 1200px; overflow: hidden; }
  body {
    background: var(--backdrop);
    font-family: "Roboto", Arial, sans-serif;
    color: var(--white);
    position: relative;
  }
  .card {
    position: absolute;
    left: 90px;
    width: 620px;
    height: 354px;
    background: var(--card);
    border-radius: 4px;
    overflow: hidden;
  }
  .card--front { top: 150px; }
  .card--back { top: 700px; }

  /* Front */
  .front-brand {
    position: absolute;
    left: 0; right: 0; top: 110px;
    text-align: center;
    font-family: "Montserrat", Arial, sans-serif;
    font-weight: 600;
    font-size: 46px;
    letter-spacing: 0.5px;
    color: var(--mauve);
  }
  .front-social {
    position: absolute;
    left: 0; right: 0; top: 232px;
    display: flex;
    justify-content: center;
    gap: 30px;
    font-size: 17px;
  }
  .handle { display: flex; align-items: center; gap: 8px; }
  .mark-square, .mark-circle {
    width: 13px; height: 13px;
    background: var(--mauve);
    flex: none;
  }
  .mark-square { border-radius: 2px; }
  .mark-circle { border-radius: 50%; }

  /* Back */
  .holder {
    position: absolute; left: 40px; top: 38px;
  }
  .holder-name {
    font-family: "Montserrat", Arial, sans-serif;
    font-weight: 700;
    font-size: 20px;
    color: var(--mauve);
  }
  .holder-role { font-size: 12px; margin-top: 3px; }
  .company {
    position: absolute; left: 40px; top: 138px;
  }
  .company-name {
    font-family: "Montserrat", Arial, sans-serif;
    font-weight: 700;
    font-size: 17px;
    color: var(--mauve);
    margin-bottom: 8px;
  }
  .contact-list { list-style: none; font-size: 14px; line-height: 20px; }
  .contact-list li { display: flex; align-items: center; gap: 9px; }
  .contact-list svg, .contact-list .mark-square, .contact-list .mark-circle {
    width: 11px; height: 11px; flex: none;
  }
  .back-brand {
    position: absolute; right: 36px; top: 120px;
    width: 220px;
    text-align: right;
    font-family: "Montserrat", Arial, sans-serif;
    font-weight: 600;
    font-size: 34px;
    line-height: 40px;
    color: var(--mauve);
  }
  .tagline-band {
    position: absolute; right: 0; bottom: 0;
    width: 320px; height: 46px;
  }
  .tagline {
    position: absolute; right: 26px; bottom: 13px;
    font-size: 16px;
    color: var(--white);
    white-space: nowrap;
  }
</style>
</head>
<body>

<section class="card card--front" aria-label="Business card front">
  <div class="front-brand">RW Office Partners</div>
  <div class="front-social">
    <span class="handle"><span class="mark-square"></span>@rwofficepartners</span>
    <span class="handle"><span class="mark-circle"></span>@rwofficepartners</span>
  </div>
</section>

<section class="card card--back" aria-label="Business card back">
  <div class="holder">
    <p class="holder-name">Marisol Wrenfield</p>
    <p class="holder-role">Virtual Assistant</p>
  </div>

  <div class="company">
    <p class="company-name">RW Office Partners</p>
    <ul class="contact-list">
      <li>
        <svg viewBox="0 0 12 12" aria-hidden="true"><path d="M2 1h2.5l1 3-1.5 1a7 7 0 0 0 3 3l1-1.5 3 1V10a1 1 0 0 1-1 1A9 9 0 0 1 1 2a1 1 0 0 1 1-1z" fill="#ddccd3"/></svg>
        61 482 907 236
      </li>
      <li>
        <svg viewBox="0 0 12 12" aria-hidden="true"><rect x="0.5" y="2" width="11" height="8" rx="1" fill="#ddccd3"/><path d="M1 2.5l5 4 5-4" stroke="#222023" stroke-width="1" fill="none"/></svg>
        marisol@rwofficepartners.com.au
      </li>
      <li>
        <svg viewBox="0 0 12 12" aria-hidden="true"><circle cx="6" cy="6" r="5" fill="none" stroke="#ddccd3" stroke-width="1.2"/><path d="M1 6h10M6 1c-2.5 3-2.5 7 0 10M6 1c2.5 3 2.5 7 0 10" stroke="#ddccd3" stroke-width="1" fill="none"/></svg>
        www.rwofficepartners.com.au
      </li>
      <li><span class="mark-square"></span>@rwofficepartners</li>
      <li><span class="mark-circle"></span>@rwofficepartners</li>
    </ul>
  </div>

  <div class="back-brand">RW Office Partners</div>

  <svg class="tagline-band" viewBox="0 0 320 46" preserveAspectRatio="none" aria-hidden="true">
    <path d="M28 0H320V46H0L16 8A14 14 0 0 1 28 0Z" fill="#986474"/>
  </svg>
  <p class="tagline">Your steady, sorted task helper</p>
</section>

</body>
</html>
```